Marava Cove Lodge Christmas wishes 2013

We require postcards designed to mail our to our clients for Christmas. We are a SURF travel company, with a high end market and like to mail our Christmas postcards to all our guests that have stayed with us through the year. Front cover will have images and text (ie Seasons Greeting) and our logo. The back will have space for TO: name & address and postage stamp. Will also have some basic text (ie The Management & Staff at Marava Cove Lodge wish you and your family all the best for the Festive Season and New Year. We look forward to seeing you back at Marava Cove Lodge again soon etc etc). Here is link to main image https://www.filecrate-example.com/sh/qwmxrtz481plo/Vb7kRtPwqN

Target Market(s)

Our clients are mostly mature men (40-70) surfers who purchase luxury surf trips

Industry/Entity Type

Travel

Requirements
Must have
• Ocean Image (front)
Logo x 2 in same colour - Orindel & Marava Cove Lodge (front)
Text (front)
Back to be white
Space for name & address (back)
Space for postage stamp (back)
Message (back)
Website www.orindellodges-example.com (back)

```html
<!DOCTYPE html>
<html lang="en">
<head>
<meta charset="utf-8">
<title>Marava Cove Lodge – Season's Greetings Postcard</title>
<link href="https://fonts.googleapis.com/css2?family=Exo+2:wght@300;400;700&display=swap" rel="stylesheet">
<style>
  :root {
    --paper: #ffffff;
    --ink-grey: #6f6f6f;
    --ink-light: #9a9a9a;
    --rule: #3a3a3a;
    --stamp-line: #8a8a8a;
    --divider: #5b3d63;
    --ocean-deep: #0b2f6b;
    --ocean-mid: #1a6fb5;
    --ocean-light: #8fd0ee;
    --foam: #f3f5f7;
    --greeting: #7fc4f2;
    --brand: #6e4a60;
  }
  html, body { margin: 0; padding: 0; overflow: hidden; }
  body { width: 891px; height: 1200px; background: var(--paper); font-family: "Exo 2", sans-serif; }
  .postcard { position: relative; width: 891px; height: 1200px; overflow: hidden; background: var(--paper); }

  /* Back side */
  .back { position: absolute; inset: 0 0 593px 0; }
  .site-url { position: absolute; left: 33px; top: 22px; font-size: 14.5px; font-weight: 300; color: var(--ink-light); margin: 0; }
  .stamp-box { position: absolute; left: 752px; top: 37px; width: 101px; height: 126px; border: 1.5px solid var(--stamp-line); border-radius: 2px; box-sizing: border-box; }
  .message { position: absolute; left: 250px; top: 80px; width: 400px; margin: 0; }
  .quote-mark { position: absolute; font-size: 80px; line-height: 1; color: var(--ink-grey); font-weight: 700; }
  .quote-open { left: 0; top: -10px; }
  .quote-close { left: 336px; top: 100px; }
  .message-text { margin: 0; padding-top: 20px; text-align: center; font-size: 18px; font-weight: 300; line-height: 25.5px; color: var(--ink-grey); }
  .signature { position: absolute; left: 0; right: 0; top: 275px; margin: 0; text-align: center; padding-right: 10px; font-size: 13px; font-weight: 300; color: var(--ink-light); }
  .address-lines { position: absolute; left: 277px; top: 394px; width: 361px; }
  .address-line { height: 0; border-top: 1.5px solid var(--rule); margin-bottom: 35px; }

  /* Front side */
  .front { position: absolute; left: 0; top: 607px; width: 891px; height: 593px; border-top: 2px solid var(--divider); box-sizing: border-box; }
  .ocean-photo { position: absolute; inset: 0;
    background:
      linear-gradient(90deg, var(--foam) 0%, var(--foam) 19%, rgba(243,245,247,0) 28%),
      radial-gradient(ellipse 40% 45% at 62% 55%, #cfeefa 0%, #7cc7ea 35%, rgba(40,130,200,0) 75%),
      radial-gradient(ellipse 35% 60% at 92% 35%, #e9f7fd 0%, rgba(160,215,240,0.6) 45%, rgba(60,140,200,0) 80%),
      linear-gradient(180deg, var(--ocean-deep) 0%, var(--ocean-mid) 45%, #2a8cd0 75%, #1a5fae 100%); }
  .greeting { position: absolute; left: 200px; top: 165px; width: 560px; margin: 0; text-align: center; font-size: 47px; font-weight: 300; color: var(--greeting); text-shadow: 0 1px 2px rgba(255,255,255,0.7), 0 0 6px rgba(10,40,100,0.35); }
  .brand-group { position: absolute; left: 151px; top: 358px; transform: translate(-50%, -50%) rotate(-90deg); white-space: nowrap; font-size: 16px; font-weight: 400; letter-spacing: 2px; color: var(--brand); margin: 0; }
  .lodge-site { position: absolute; left: 60px; top: 407px; transform: translate(-50%, -50%) rotate(-90deg); white-space: nowrap; text-align: center; color: var(--brand); font-size: 12px; font-weight: 400; line-height: 14px; margin: 0; }
  .badge { position: absolute; left: 11px; width: 32px; height: 32px; border-radius: 50%; border: 2.5px solid var(--brand); box-sizing: border-box; }
</style>
</head>
<body>
<main class="postcard">
  <section class="back">
    <p class="site-url">www.orindellodges-example.com</p>
    <div class="stamp-box" aria-label="Postage stamp"></div>
    <blockquote class="message">
      <span class="quote-mark quote-open">&ldquo;</span>
      <p class="message-text">Wish you and your family all the best<br>for the Festive Season and New Year.<br>We look forward to seeing you back at<br>Marava Cove Lodge again soon...</p>
      <span class="quote-mark quote-close">&rdquo;</span>
    </blockquote>
    <p class="signature">The Management &amp; Staff at Marava Cove Lodge</p>
    <div class="address-lines" aria-label="Recipient name and address">
      <div class="address-line"></div>
      <div class="address-line"></div>
      <div class="address-line"></div>
      <div class="address-line"></div>
    </div>
  </section>

  <section class="front">
    <div class="ocean-photo" role="img" aria-label="Photograph of a surfer riding inside a large curling blue ocean wave, with a white surfboard along the left edge"></div>
    <h1 class="greeting">Season’s Greetings</h1>
    <p class="brand-group">ORINDEL&nbsp; LODGES &amp; RESORTS</p>
    <span class="badge" style="top:350px;"></span>
    <span class="badge" style="top:387px;"></span>
    <span class="badge" style="top:431px;"></span>
    <p class="lodge-site">maravacovelodge-example.com<br>indonesia</p>
  </section>
</main>
</body>
</html>
```